Canadian company needs a packaging design for a new product line of TubGlow Hot Tub & Bath Fragran

We are looking for a packaging design for a new company based in Edmonton, Alberta Canada called TubGlow. We are developing a new product line of liquid and crystal Hot Tub & Bath Fragrances (aromatherapy) for example Lavender will be one of our fragrances. We are looking at the possibilities of using a stand up pouch and or the standard plastic bottles for our fragrance line. There will be different sizes from 150 grams to 600 grams in the crystal and 275 ml in the liquid. We would like to see bright multi-colored designs possibly with picture of the fragrance or a theme like favorite drinks or a more sensual idea. Each one of our fragrances will be a different color the main design needs to be able to have a different color of liquid or crystal in the bottle and possibly parts of the label will change colors for each fragrance. I have attached samples of another brand that we want to improve on.

Target Market(s)

Most of these fragrance are bought by women 70% men 30%
age 25 - 55

Industry/Entity Type

It Company

Requirements
Must have
• bottle size
Fragrance name
Nice to have
• Using the files below I like the circle of colors and possibly it could be made using water drops like in the file and possibly the two "S" could be designed like the third file I just added

Files

```html
<!DOCTYPE html>
<html lang="en">
<head>
<meta charset="utf-8">
<title>TubGlow Packaging Labels</title>
<link rel="stylesheet" href="https://fonts.googleapis.com/css2?family=Marcellus&family=Roboto+Condensed:wght@400;700&display=swap">
<style>
  :root {
    --bg: #ffffff;
    --lav-deep: #4b2a7a;
    --lav-light: #d9c4ee;
    --lav-pale: #f3ecf8;
    --lav-pink: #f2b8ee;
    --org-deep: #e0601a;
    --org-mid: #f59a1c;
    --org-light: #ffd23a;
    --org-pale: #fff4b8;
    --ink: #1b1b1b;
    --white: #ffffff;
    --silver-dark: #8e9296;
    --silver-light: #eef0f2;
    --glass-edge: #c9ccd0;
  }
  * { margin: 0; padding: 0; box-sizing: border-box; }
  html, body { width: 1200px; height: 900px; overflow: hidden; background: var(--bg); }
  .canvas { position: relative; width: 1200px; height: 900px; background: var(--bg); }

  .bottle { position: absolute; }
  .spray-bottle { width: 138px; height: 653px; top: 42px; }
  .jar { width: 205px; height: 482px; top: 218px; }

  .overcap {
    position: absolute; left: 0; top: 0; width: 138px; height: 146px;
    border: 1px solid var(--glass-edge); border-radius: 3px;
    background: linear-gradient(90deg, rgba(210,214,218,0.55), rgba(255,255,255,0.2) 30%, rgba(255,255,255,0.1) 70%, rgba(200,204,208,0.55));
  }
  .pump-head {
    position: absolute; left: 40px; top: 20px; width: 58px; height: 40px;
    background: linear-gradient(90deg, var(--silver-dark), var(--silver-light) 40%, #b8bcc0 75%, var(--silver-dark));
    border-radius: 2px;
  }
  .pump-collar {
    position: absolute; left: 33px; top: 60px; width: 72px; height: 80px;
    background: linear-gradient(90deg, var(--silver-dark), var(--silver-light) 35%, #c4c8cc 70%, var(--silver-dark));
  }
  .jar-cap {
    position: absolute; left: 15px; top: 0; width: 175px; height: 34px;
    border-radius: 6px 6px 2px 2px;
    background: linear-gradient(90deg, var(--silver-dark), var(--silver-light) 30%, #c4c8cc 60%, var(--silver-light) 80%, var(--silver-dark));
  }

  .label { position: absolute; overflow: hidden; }
  .spray-label { left: 0; top: 138px; width: 138px; height: 515px; border-radius: 0 0 10px 10px; }
  .jar-label { left: 0; top: 32px; width: 205px; height: 450px; border-radius: 10px 10px 16px 16px; }

  .crystals { position: absolute; left: 0; width: 100%; }
  .crystals-top { top: 0; height: 47px; }
  .crystals-bottom { bottom: 0; height: 88px; }
  .jar-band { position: absolute; left: 0; top: 47px; width: 100%; height: 315px; }

  .lavender .spray-label { background: linear-gradient(90deg, #b894d6, var(--lav-light) 45%, #c6a6e0); }
  .lavender .jar-band { background: linear-gradient(180deg, var(--lav-pink), var(--lav-pale) 45%, #f4f0f6); }
  .lavender .crystals { background: linear-gradient(180deg, #b89ce0, #8a6cc8); }
  .orange .spray-label { background: linear-gradient(90deg, var(--org-deep), var(--org-mid) 35%, var(--org-light) 70%, #f6a21c); }
  .orange .jar-band { background: linear-gradient(90deg, var(--org-pale), #fffbe6 50%, #ffe27a); }
  .orange .crystals { background: linear-gradient(180deg, #f2b48a, #e0906a); }

  .wordmark {
    position: absolute;
    writing-mode: vertical-rl;
    transform: rotate(180deg);
    font-family: "Marcellus", serif;
    font-size: 62px;
    line-height: 1;
    white-space: nowrap;
  }
  .tagline {
    position: absolute;
    writing-mode: vertical-rl;
    font-family: "Roboto Condensed", sans-serif;
    font-weight: 700;
    font-size: 9px;
    letter-spacing: 0.5px;
    color: var(--ink);
    white-space: nowrap;
  }
  .lavender .wordmark { color: var(--lav-deep); }
  .orange .spray-label .wordmark { color: var(--ink); }
  .orange .jar-label .wordmark { color: var(--org-deep); }

  .scent-pill {
    position: absolute;
    font-family: "Marcellus", serif;
    font-size: 14px;
    color: var(--white);
    padding: 2px 10px;
    border-radius: 11px;
    white-space: nowrap;
  }
  .lavender .scent-pill { background: var(--lav-deep); }
  .orange .scent-pill { background: var(--org-deep); }

  .blurb {
    position: absolute;
    font-family: "Roboto Condensed", sans-serif;
    font-size: 8px;
    line-height: 1.15;
    text-align: center;
    white-space: nowrap;
  }
  .spray-label .blurb { color: var(--white); width: 100%; left: 0; }
  .orange .spray-label .blurb { color: var(--ink); }
  .jar-label .blurb { color: var(--ink); }
  .volume {
    position: absolute;
    font-family: "Roboto Condensed", sans-serif;
    font-weight: 700;
    font-size: 10px;
    color: var(--ink);
  }
  .art { position: absolute; }
  .lavender .art { background: linear-gradient(160deg, rgba(200,170,230,0), #9a7ac4 55%, #6a4a9c); }
  .orange .art { background: radial-gradient(circle at 60% 55%, #ffb21c, #f08a12 55%, #7aa33a); }
</style>
</head>
<body>
<main class="canvas">

  <section class="product-set lavender">
    <div class="bottle spray-bottle" style="left:222px">
      <div class="overcap"></div>
      <div class="pump-head"></div>
      <div class="pump-collar"></div>
      <article class="label spray-label">
        <div class="art" style="left:0; top:360px; width:138px; height:155px" role="img" aria-label="Lavender sprigs photograph"></div>
        <div class="wordmark" style="left:40px; top:50px">TubGlow</div>
        <div class="tagline" style="left:100px; top:57px">SPA &amp; BATH FRAGRANCE</div>
        <div class="scent-pill" style="left:32px; top:317px">Lavender</div>
        <p class="blurb" style="top:342px">Aromatherapy with<br>formulation lorem ipsum</p>
        <div class="volume" style="left:56px; top:370px">175ml</div>
      </article>
    </div>

    <div class="bottle jar" style="left:383px">
      <div class="jar-cap"></div>
      <article class="label jar-label">
        <div class="crystals crystals-top" role="img" aria-label="Purple bath crystals"></div>
        <div class="jar-band">
          <div class="art" style="left:70px; top:133px; width:135px; height:182px" role="img" aria-label="Lavender sprigs photograph"></div>
          <div class="wordmark" style="left:17px; top:30px">TubGlow</div>
          <div class="tagline" style="left:78px; top:38px">SPA &amp; BATH FRAGRANCE</div>
          <div class="scent-pill" style="left:117px; top:43px">Lavender</div>
          <p class="blurb" style="left:112px; top:73px">Aromatherapy with<br>formulation lorem ipsum</p>
          <div class="volume" style="left:165px; top:300px">250ml</div>
        </div>
        <div class="crystals crystals-bottom" role="img" aria-label="Purple bath crystals"></div>
      </article>
    </div>
  </section>

  <section class="product-set orange">
    <div class="bottle spray-bottle" style="left:671px">
      <div class="overcap"></div>
      <div class="pump-head"></div>
      <div class="pump-collar"></div>
      <article class="label spray-label">
        <div class="art" style="left:0; top:375px; width:138px; height:140px" role="img" aria-label="Sliced oranges with leaves photograph"></div>
        <div class="wordmark" style="left:40px; top:50px">TubGlow</div>
        <div class="tagline" style="left:100px; top:57px">SPA &amp; BATH FRAGRANCE</div>
        <div class="scent-pill" style="left:36px; top:317px">Orange</div>
        <p class="blurb" style="top:342px">Aromatherapy with<br>formulation lorem ipsum</p>
        <div class="volume" style="left:56px; top:370px">175ml</div>
      </article>
    </div>

    <div class="bottle jar" style="left:832px">
      <div class="jar-cap"></div>
      <article class="label jar-label">
        <div class="crystals crystals-top" role="img" aria-label="Orange bath crystals"></div>
        <div class="jar-band">
          <div class="art" style="left:70px; top:165px; width:135px; height:150px" role="img" aria-label="Sliced oranges and lemon with leaves photograph"></div>
          <div class="wordmark" style="left:17px; top:30px">TubGlow</div>
          <div class="tagline" style="left:78px; top:38px">SPA &amp; BATH FRAGRANCE</div>
          <div class="scent-pill" style="left:120px; top:43px">Orange</div>
          <p class="blurb" style="left:112px; top:73px">Aromatherapy with<br>formulation lorem ipsum</p>
          <div class="volume" style="left:165px; top:300px">250ml</div>
        </div>
        <div class="crystals crystals-bottom" role="img" aria-label="Orange bath crystals"></div>
      </article>
    </div>
  </section>

</main>
</body>
</html>
```